Business Card Design for my Real Estate Investing Company

This is for a Real Estate Investing Company that will be serving the Las Vegas Valley. Id like the following slogan included: Building Homes, Building Trust I have attached my logo. You will see the color tones I'm interested in..in my logo. I would like the card to be double-sided with a modern, professional look.
Target Market(s)
Homeowners, banks, real estate industry
Industry/Entity Type
Real Estate
Contact Information for Business Card
name: Dale Harwick
position: Managing Member
address: 4821 Corliss Pkwy ste 207-300
Ridgemont, NV 89370
phone: (702) 555-0143
fax: (702) 555-0187
email: SummitRidgeEstate@hollowmail.test
web: SummitRidgeEstates.test
*At the bottom of the card I would like....
We buy houses for cash....no repairs, no commissions, no fees!
Logo Text
SUMMIT RIDGE ESTATES "Investing in Our Community"
Font styles to use
Other font styles liked:
- Lora
Requirements
Must have
- On the back of the card, i'd like to have my logo large and the following statements:
- Are you considering selling your home? Want a simple, hassle-free transaction? We can help! We buy houses for cash and can close quickly! No need to do any repairs, no realtor commissions, no closing costs.....and no headaches. Let us help you with your real estate needs...!
Nice to have
- multiple colors 2 two tone on front and back

```html
<!DOCTYPE html>
<html lang="en">
<head>
<meta charset="utf-8">
<title>Summit Ridge Estates – Business Card</title>
<link href="https://fonts.googleapis.com/css2?family=Lora:wght@400;600&display=swap" rel="stylesheet">
<style>
  :root {
    --brand-blue: #0b5aa8;
    --ink-dark: #2e2e2e;
    --paper: #ffffff;
    --backdrop: #3a3a3a;
  }
  html, body {
    margin: 0;
    padding: 0;
    width: 1189px;
    height: 1200px;
    overflow: hidden;
    background: var(--backdrop);
    font-family: "Lora", Georgia, serif;
  }
  .card {
    position: absolute;
    left: 171px;
    width: 855px;
    height: 488px;
    overflow: hidden;
    box-shadow: 0 6px 18px rgba(0,0,0,0.45);
  }
  .card--front { top: 67px; background: var(--brand-blue); color: var(--paper); }
  .card--back { top: 626px; background: var(--paper); }

  .wordmark {
    display: flex;
    align-items: center;
    gap: 12px;
    font-weight: 600;
    font-size: 38px;
    letter-spacing: 1px;
    white-space: nowrap;
  }
  .wordmark__square { width: 26px; height: 26px; flex: none; }
  .motto {
    font-size: 17px;
    letter-spacing: 1px;
    white-space: nowrap;
  }

  .card--front .brand {
    position: absolute;
    top: 232px;
    left: 0;
    width: 100%;
    display: flex;
    flex-direction: column;
    align-items: center;
    gap: 12px;
  }
  .card--front .wordmark__square { background: var(--paper); }
  .offer {
    position: absolute;
    top: 368px;
    margin: 0;
    width: 100%;
    text-align: center;
    font-size: 21px;
  }

  .swoosh { position: absolute; inset: 0; }
  .card--back .brand {
    position: absolute;
    top: 122px;
    left: 60px;
    display: flex;
    flex-direction: column;
    align-items: flex-start;
    gap: 12px;
  }
  .card--back .wordmark { color: var(--brand-blue); }
  .card--back .wordmark__square { background: var(--brand-blue); }
  .card--back .motto { color: var(--ink-dark); }

  .contact {
    position: absolute;
    right: 38px;
    top: 192px;
    text-align: right;
    color: var(--paper);
  }
  .contact__name { font-size: 27px; font-weight: 600; line-height: 1.1; text-transform: uppercase; }
  .contact__role { font-size: 20px; line-height: 1.2; }
  .contact__address { margin-top: 24px; font-size: 21px; line-height: 1.3; }
  .contact__lines { margin: 8px 0 0; list-style: none; padding: 0; }
  .contact__lines li {
    display: flex;
    justify-content: flex-end;
    align-items: center;
    gap: 12px;
    font-size: 21px;
    line-height: 27px;
  }
  .icon { width: 20px; height: 20px; flex: none; }
</style>
</head>
<body>

<section class="card card--front" aria-label="Card front">
  <div class="brand">
    <div class="wordmark"><span class="wordmark__square"></span>SUMMIT RIDGE ESTATES</div>
    <div class="motto">Building Homes, Building Trust</div>
  </div>
  <p class="offer">We buy houses for cash....no repairs, no commissions, no fees</p>
</section>

<section class="card card--back" aria-label="Card back">
  <svg class="swoosh" viewBox="0 0 855 488" width="855" height="488" aria-hidden="true">
    <path d="M708 0 C650 190 420 420 73 488 L855 488 L855 0 Z" fill="var(--brand-blue)"/>
    <path d="M681 52 C560 270 330 440 0 488 L40 488 C370 430 585 280 681 52 Z" fill="var(--ink-dark)"/>
  </svg>

  <div class="brand">
    <div class="wordmark"><span class="wordmark__square"></span>SUMMIT RIDGE ESTATES</div>
    <div class="motto">Building Homes, Building Trust</div>
  </div>

  <div class="contact">
    <div class="contact__name">Dale Harwick</div>
    <div class="contact__role">Managing Member</div>
    <div class="contact__address">4821 Corliss Pkwy ste 207-300<br>Ridgemont, NV 89370</div>
    <ul class="contact__lines">
      <li>(702) 555-0143
        <svg class="icon" viewBox="0 0 20 20" aria-label="Mobile"><rect width="20" height="20" rx="2" fill="#fff"/><rect x="6" y="3" width="8" height="14" rx="1" fill="none" stroke="var(--brand-blue)" stroke-width="1.5"/><circle cx="10" cy="14.5" r="1" fill="var(--brand-blue)"/></svg>
      </li>
      <li>(702) 555-0187
        <svg class="icon" viewBox="0 0 20 20" aria-label="Phone"><rect width="20" height="20" rx="2" fill="#fff"/><path d="M3 8 Q10 3 17 8 L15 10 L13 8 L7 8 L5 10 Z" fill="var(--brand-blue)"/><rect x="5" y="11" width="10" height="5" rx="1" fill="var(--brand-blue)"/></svg>
      </li>
      <li>SummitRidgeEstate@hollowmail.test
        <svg class="icon" viewBox="0 0 20 20" aria-label="Email"><rect width="20" height="20" rx="2" fill="#fff"/><rect x="3" y="5" width="14" height="10" fill="none" stroke="var(--brand-blue)" stroke-width="1.5"/><path d="M3 5 L10 11 L17 5" fill="none" stroke="var(--brand-blue)" stroke-width="1.5"/></svg>
      </li>
      <li>SummitRidgeEstates.test
        <svg class="icon" viewBox="0 0 20 20" aria-label="Website"><rect width="20" height="20" rx="2" fill="#fff"/><circle cx="10" cy="10" r="6.5" fill="none" stroke="var(--brand-blue)" stroke-width="1.4"/><ellipse cx="10" cy="10" rx="3" ry="6.5" fill="none" stroke="var(--brand-blue)" stroke-width="1.2"/><path d="M3.5 10 H16.5" stroke="var(--brand-blue)" stroke-width="1.2"/></svg>
      </li>
    </ul>
  </div>
</section>

</body>
</html>
```